Bright and beautiful business card for a coach

I'm a personal and business coach based in Perth, Australia. I need a business card that whilst subtle and elegant, will stand out and appeal on a table full of cards.

My business name is Fern Mentoring and the business card must represent the warmth and brightness implied in the name, without being gimmicky. It must have a warmth and appeal and be easy to read.

I prefer clean, minimalist designs.

It must align with the feel of my website and socials: https://www.fernmentoring-example.com.au/
https://www.instagram.com/fernmentoringau/
https://www.facebook.com/fernmentoringau
Updates

Hi Designers Thank you so much for taking the time to submit designs. I wonder if I could have explained myself a little better. Most of the designs that have been submitted look rather formal and many have quite corporate looking embellishments on them (to my eye). I would like softer, warmer, more organic. I’m open to people playing about and being more abstract, using softer embellishments (e.g the line drawing flowers and grasses I’ve used in my socials) incorporating other colours from my palette or like the social icons in my email signature (in PDF), perhaps playing with size/oversize, playing with the bleed. Please don’t be constrained by what I’ve already done, it merely needs to compliment. I’m sorry if I’m not using the right words or have led you astray. I’m no designer, but I’ve done my website, socials, email signature etc all myself (my logo was a design contest) and I was really hoping for my business card to be something more creative than I could have made with a template. Reminder: No black cards/sides please. Thank you 😊

Target Market(s)

Individuals, most likely but not all female. Creative thinkers. Likely professionals.

Industry/Entity Type

Business & Personal Coach

Contact Information for Business Card

(Fern Mentoring Logo) Name: Greta Pellham; Title: Business & Personal Coach; Phone number: +61 (0)458 913307; Email: greta@fernmentoring-example.com.au; Website: https://fernmentoring-example.com.au; Social icons for Facebook, Instagram & LinkedIn: @fernmentoringAU. Optional strapline: "A thinking partner to help you cut through the noise"

Font styles to use
Sans Serif

Colors
00AB8E
00BBA5
67D7C9
C6EFE9
E9F9F6
59FF00
82FF00
B8FF75
E3FFCB
F4FFEA
FFC000
F8CF3A
FAE287
FDF2CF
FEFAEE

Requirements
Must have
• Must align with feel of my website and socials. Must have a pop of #FFC000 (possibly whole of one side, or at least a block). Bright or white background. Easy to read.
Nice to have
• Possibly incorporate the sunshine/grass picture I have used in website and socials - will upload.
Should not have
• Must not be black or dark. Not impersonal or corporate looking.

```html
<!DOCTYPE html>
<html lang="en">
<head>
<meta charset="utf-8">
<title>Fern Mentoring — Business Card</title>
<link href="https://fonts.googleapis.com/css2?family=Montserrat:wght@400;500;600;700&display=swap" rel="stylesheet">
<style>
  :root {
    --sun: #FFC000;
    --sun-soft: #F8CF3A;
    --sun-pale: #FAE287;
    --paper: #FBF9F6;
    --ink: #5E5E5E;
    --ink-soft: #6B6B6B;
    --page: #FFFFFF;
  }
  * { margin: 0; padding: 0; box-sizing: border-box; }
  html, body {
    width: 687px;
    height: 1200px;
    overflow: hidden;
    background: var(--page);
    font-family: "Montserrat", sans-serif;
  }
  .sheet {
    position: relative;
    width: 687px;
    height: 1200px;
  }
  .card {
    position: absolute;
    left: 33px;
    width: 620px;
    height: 355px;
    background: var(--paper);
    box-shadow: 0 2px 6px rgba(0,0,0,0.18);
    overflow: hidden;
  }
  .card--front { top: 205px; }
  .card--back { top: 640px; }
  .card__shapes {
    position: absolute;
    inset: 0;
    width: 100%;
    height: 100%;
  }
  .wordmark {
    position: absolute;
    display: flex;
    align-items: center;
    gap: 10px;
    color: var(--sun);
    font-weight: 500;
    white-space: nowrap;
  }
  .wordmark__dot {
    border-radius: 50%;
    background: var(--sun);
    flex: none;
  }
  .card--front .wordmark {
    left: 0; right: 0;
    top: 118px;
    justify-content: center;
    font-size: 42px;
    letter-spacing: 0.5px;
  }
  .card--front .wordmark__dot { width: 22px; height: 22px; }
  .front-url {
    position: absolute;
    left: 0; right: 0;
    top: 250px;
    text-align: center;
    color: var(--sun);
    font-weight: 600;
    font-size: 15px;
    letter-spacing: 0.3px;
  }
  .card--back .wordmark {
    right: 24px;
    top: 90px;
    font-size: 24px;
    gap: 8px;
  }
  .card--back .wordmark__dot { width: 13px; height: 13px; }
  .person {
    position: absolute;
    left: 21px;
    top: 150px;
  }
  .person__name {
    color: var(--sun);
    font-weight: 700;
    font-size: 25px;
    line-height: 1.1;
  }
  .person__title {
    color: var(--ink);
    font-weight: 600;
    font-size: 15px;
    letter-spacing: 0.4px;
    margin-top: 2px;
  }
  .divider {
    position: absolute;
    left: 21px;
    right: 22px;
    top: 206px;
    height: 2px;
    background: var(--sun);
  }
  .contacts {
    position: absolute;
    left: 21px;
    top: 223px;
    list-style: none;
  }
  .contact {
    display: flex;
    align-items: center;
    gap: 12px;
    height: 30px;
    color: var(--ink-soft);
    font-size: 15px;
    letter-spacing: 0.3px;
  }
  .contact__icon {
    width: 26px;
    height: 26px;
    border-radius: 50%;
    background: var(--sun);
    display: flex;
    align-items: center;
    justify-content: center;
    flex: none;
  }
  .contact__icon svg { width: 15px; height: 15px; }
  .contact__accent { color: var(--sun); font-weight: 600; }
</style>
</head>
<body>
<main class="sheet">

  <!-- Front -->
  <section class="card card--front">
    <svg class="card__shapes" viewBox="0 0 944 540" preserveAspectRatio="none" aria-hidden="true">
      <path d="M0 0 H690 C560 40 420 40 300 75 C200 102 110 100 0 92 Z" fill="var(--sun)"/>
      <path d="M0 72 C120 82 210 60 330 35 C440 15 560 25 680 2" fill="none" stroke="#fff" stroke-width="4"/>
      <path d="M95 540 C220 490 430 500 560 468 C660 440 720 418 944 438 V540 Z" fill="var(--sun)"/>
    </svg>
    <svg class="card__shapes" viewBox="0 0 944 540" preserveAspectRatio="none" role="img" aria-label="Line drawing of wild flowers and grasses in white over the yellow band">
      <defs>
        <radialGradient id="bloomFront" cx="50%" cy="70%" r="60%">
          <stop offset="0" stop-color="var(--sun-pale)" stop-opacity="0.55"/>
          <stop offset="1" stop-color="var(--sun)" stop-opacity="0"/>
        </radialGradient>
      </defs>
      <rect x="700" y="390" width="244" height="150" fill="url(#bloomFront)"/>
      <rect x="150" y="470" width="210" height="70" fill="url(#bloomFront)"/>
    </svg>
    <div class="wordmark"><span class="wordmark__dot"></span>Fern Mentoring</div>
    <p class="front-url">www.fernmentoring-example.com.au</p>
  </section>

  <!-- Back -->
  <section class="card card--back">
    <svg class="card__shapes" viewBox="0 0 944 540" preserveAspectRatio="none" aria-hidden="true">
      <path d="M365 0 H944 V95 C850 60 760 35 640 32 C540 30 450 25 365 0 Z" fill="var(--sun)"/>
      <path d="M395 5 C470 25 560 22 660 26 C770 32 860 65 944 92" fill="none" stroke="#fff" stroke-width="4"/>
      <path d="M105 540 C230 492 430 500 560 470 C660 445 720 420 944 440 V540 Z" fill="var(--sun)"/>
    </svg>
    <svg class="card__shapes" viewBox="0 0 944 540" preserveAspectRatio="none" role="img" aria-label="Line drawing of wild flowers and grasses in white over the yellow band">
      <defs>
        <radialGradient id="bloomBack" cx="50%" cy="70%" r="60%">
          <stop offset="0" stop-color="var(--sun-pale)" stop-opacity="0.55"/>
          <stop offset="1" stop-color="var(--sun)" stop-opacity="0"/>
        </radialGradient>
      </defs>
      <rect x="700" y="395" width="244" height="145" fill="url(#bloomBack)"/>
      <rect x="150" y="475" width="210" height="65" fill="url(#bloomBack)"/>
    </svg>

    <div class="wordmark"><span class="wordmark__dot"></span>Fern Mentoring</div>

    <div class="person">
      <h1 class="person__name">Greta Pellham</h1>
      <p class="person__title">Business &amp; Personal Coach</p>
    </div>
    <div class="divider"></div>

    <ul class="contacts">
      <li class="contact">
        <span class="contact__icon">
          <svg viewBox="0 0 24 24" aria-hidden="true"><path d="M6.6 10.8a15.1 15.1 0 0 0 6.6 6.6l2.2-2.2a1 1 0 0 1 1-.25 11.4 11.4 0 0 0 3.6.57 1 1 0 0 1 1 1V20a1 1 0 0 1-1 1A17 17 0 0 1 3 4a1 1 0 0 1 1-1h3.5a1 1 0 0 1 1 1c0 1.25.2 2.45.57 3.57a1 1 0 0 1-.25 1z" fill="none" stroke="#fff" stroke-width="1.8"/></svg>
        </span>
        +61 (0)458 913307
      </li>
      <li class="contact">
        <span class="contact__icon">
          <svg viewBox="0 0 24 24" aria-hidden="true"><rect x="3" y="5.5" width="18" height="13" rx="1.5" fill="none" stroke="#fff" stroke-width="1.8"/><path d="M3.5 6.5 12 13l8.5-6.5" fill="none" stroke="#fff" stroke-width="1.8"/></svg>
        </span>
        greta@fernmentoring-example.com.au
      </li>
      <li class="contact">
        <span class="contact__icon">
          <svg viewBox="0 0 24 24" aria-hidden="true"><circle cx="12" cy="12" r="9" fill="none" stroke="#fff" stroke-width="1.8"/><ellipse cx="12" cy="12" rx="4" ry="9" fill="none" stroke="#fff" stroke-width="1.6"/><path d="M3 12h18M4.5 7.5h15M4.5 16.5h15" stroke="#fff" stroke-width="1.4"/></svg>
        </span>
        <span>www.<span class="contact__accent">fernmentoring-example.com.au</span></span>
      </li>
    </ul>
  </section>

</main>
</body>
</html>
```